Quill Physical Therapy Website

I would need a clean modern website built to showcase my Physical therapy brand and services. I would need a simple but descriptive website that can ultimately connect my patients to my electronic medical portal so they may book an appointment..

```html
<!DOCTYPE html>
<html lang="en">
<head>
<meta charset="utf-8">
<title>Quill Physical Therapy &amp; Wellness</title>
<link href="https://fonts.googleapis.com/css2?family=Montserrat:wght@400;500;600;700;800&family=Lato:ital,wght@0,400;0,700;1,400&display=swap" rel="stylesheet">
<style>
:root{
  --teal:#138581;
  --teal-dark:#0c6b68;
  --green:#7cc458;
  --green-light:#8fcf62;
  --blue:#4a5ba8;
  --ink:#2b3038;
  --body:#5a6068;
  --muted:#8a9097;
  --hero-bg:#edf3f3;
  --mint:#eaf6f5;
  --line:#d5d9dd;
  --foot-bar:#e3e7f0;
}
*{margin:0;padding:0;box-sizing:border-box}
html,body{width:1200px;height:4367px;overflow:hidden}
body{position:relative;background:#fff;font-family:'Lato',sans-serif;color:var(--ink)}
.abs{position:absolute}
.head-font{font-family:'Montserrat',sans-serif}
.photo{position:absolute}

/* header */
.site-header{position:absolute;left:0;top:0;width:1200px;height:114px;background:#fff;z-index:3}
.nav{position:absolute;top:72px;font-family:'Montserrat',sans-serif;font-size:12.5px;font-weight:500;color:var(--ink);letter-spacing:.2px}
.nav.active{color:var(--teal)}
.nav.active::after{content:"";position:absolute;left:0;right:0;top:36px;height:3px;background:var(--green)}
.call-btn{position:absolute;left:800px;top:0;width:282px;height:43px;background:var(--teal);color:#fff;font-family:'Montserrat',sans-serif;font-weight:600;font-size:13.5px;display:flex;align-items:center;justify-content:center;gap:8px;letter-spacing:.4px}
.brand-badge{position:absolute;left:488px;top:-26px;width:204px;height:204px;border-radius:50%;background:#fff;box-shadow:0 6px 14px rgba(0,0,0,.08);z-index:4;display:flex;flex-direction:column;align-items:center;justify-content:center;padding-top:26px}
.brand-dot{width:46px;height:46px;border-radius:50%;background:var(--teal);margin-bottom:8px}
.brand-name{font-family:'Montserrat',sans-serif;font-weight:800;font-size:34px;color:var(--teal);letter-spacing:1px}

/* hero */
.hero{position:absolute;left:0;top:114px;width:1200px;height:649px;background:var(--hero-bg)}
.hero-photo{left:560px;top:0;width:640px;height:649px;background:linear-gradient(120deg,#e9efef 0%,#d9cbc2 45%,#c7aa98 70%,#e6ecec 100%)}
.hero-kicker{left:115px;top:202px;font-family:'Montserrat',sans-serif;font-size:24px;color:var(--teal);letter-spacing:3px}
.hero-title{left:113px;top:232px;font-family:'Montserrat',sans-serif;font-weight:700;font-size:49px;color:var(--teal);letter-spacing:1.5px}
.hero-sub{left:115px;top:290px;font-family:'Montserrat',sans-serif;font-weight:700;font-size:36px;color:var(--green);letter-spacing:2px}
.btn-pill{position:absolute;border-radius:30px;font-family:'Montserrat',sans-serif;font-weight:700;letter-spacing:1px;display:flex;align-items:center;justify-content:center;gap:6px}
.hero-btn{left:117px;top:352px;width:234px;height:49px;background:var(--green);color:#fff;font-size:13px}
.hero-arrow{position:absolute;top:284px}

/* feature cards */
.feature{position:absolute;color:#fff;text-align:center;font-family:'Montserrat',sans-serif}
.feature h3{font-size:17px;font-weight:400;letter-spacing:1px;line-height:21px}
.feature h3 b{font-weight:700}
.feature p{font-family:'Lato',sans-serif;font-size:11px;line-height:15px;margin:8px auto 0;opacity:.92}
.feature .mini-btn{margin:16px auto 0;width:124px;height:32px;border:2px solid #fff;border-radius:20px;font-size:10px;font-weight:700;display:flex;align-items:center;justify-content:center;letter-spacing:.5px}
.card-green{left:108px;top:690px;width:306px;height:186px;background:var(--green);padding-top:42px}
.card-teal{left:414px;top:661px;width:340px;height:242px;background:var(--teal);padding-top:58px;box-shadow:0 10px 18px rgba(0,0,0,.18);z-index:2}
.card-teal .mini-btn{background:var(--green);border-color:var(--green);width:136px;height:34px}
.card-blue{left:754px;top:688px;width:329px;height:187px;background:var(--blue);padding-top:45px}

/* about */
.about-ring{left:65px;top:965px;width:504px;height:504px;border-radius:50%;background:#f4f5f5}
.about-ring2{left:100px;top:1000px;width:434px;height:434px;border-radius:50%;background:#e1e4e4}
.about-photo{left:122px;top:1022px;width:390px;height:390px;border-radius:50%;background:radial-gradient(circle at 45% 40%,#f1e4da 0%,#c9d9d3 55%,#9db5ac 100%)}
.kicker{position:absolute;font-family:'Montserrat',sans-serif;font-size:16px;letter-spacing:3px;color:var(--teal)}
.section-title{position:absolute;font-family:'Montserrat',sans-serif;font-weight:700;color:var(--ink);letter-spacing:1.5px}
.about-text{left:595px;top:1128px;font-size:17px;line-height:32px;color:var(--body)}
.outline-btn{left:593px;top:1324px;width:182px;height:49px;border:2px solid var(--teal);color:var(--teal);font-size:14px;background:#fff}

/* services */
.services{position:absolute;left:0;top:1487px;width:1200px;height:700px;background:var(--mint)}
.bar{position:absolute;height:4px;background:var(--green)}
.services-text{left:110px;top:1758px;font-size:17px;line-height:34px;color:var(--body)}
.services-btn{left:108px;top:1914px;width:184px;height:51px;background:var(--green);color:#fff;font-size:14px}
.services-art{left:466px;top:1600px;width:300px;height:420px;background:linear-gradient(180deg,rgba(230,233,233,.0),rgba(210,220,222,.7) 40%,rgba(200,215,217,.0))}
.services-photo{left:510px;top:1600px;width:250px;height:250px;border-radius:50%;background:radial-gradient(circle at 40% 45%,#f0e2d8,#c7d3d6 70%,#a9bcc0)}
.svc-icon{position:absolute;width:68px;height:68px;border-radius:50%;background:linear-gradient(135deg,var(--green),var(--teal));display:flex;align-items:center;justify-content:center}
.svc-title{position:absolute;font-size:17px;color:var(--ink);font-weight:700}
.svc-text{position:absolute;font-size:12.5px;line-height:17px;color:var(--muted)}

/* success stories */
.stories-band{left:0;top:2090px;width:1200px}
.band-kicker{left:0;width:1200px;text-align:center;top:2210px;color:#dff2f0;font-family:'Montserrat',sans-serif;font-size:17px;letter-spacing:3px}
.band-title{left:0;width:1200px;text-align:center;top:2236px;color:#fff;font-family:'Montserrat',sans-serif;font-weight:700;font-size:34px;letter-spacing:1.5px}
.story{position:absolute;background:#fff;box-shadow:0 4px 10px rgba(0,0,0,.15)}
.story-photo{position:absolute;left:0;top:0}
.story h4{position:absolute;font-family:'Montserrat',sans-serif;font-weight:700;color:var(--ink)}
.story p{position:absolute;color:var(--muted)}

/* reviews */
.review{position:absolute;top:2992px;width:297px;height:373px;border:2px solid #cfd3d7;border-radius:4px;background:#fff;overflow:hidden;text-align:center}
.review-photo{position:absolute;left:0;top:0;width:100%;height:188px}
.avatar{position:absolute;left:123px;top:161px;width:50px;height:50px;border-radius:50%;background:#d7dde0;border:3px solid #fff}
.review p{position:absolute;left:20px;right:20px;top:222px;font-style:italic;font-size:12.5px;line-height:19.5px;color:#6d737a}
.review .who{position:absolute;left:0;right:0;top:309px;font-family:'Montserrat',sans-serif;font-size:12px;font-weight:700;color:var(--blue)}
.review .stars{position:absolute;left:0;right:0;top:323px;font-size:21px;color:#f29a17;letter-spacing:1px}
.dot{position:absolute;top:3403px;height:3px;width:34px;background:#c6cacd}

/* appointment */
.appt{position:absolute;left:0;top:3478px;width:602px;height:519px;background:linear-gradient(180deg,var(--green-light),#74bf52)}
.appt-photo{left:602px;top:3478px;width:598px;height:519px;background:linear-gradient(110deg,#eef2f2 0%,#d9cfc9 40%,#8fb8c6 60%,#e6ecec 100%)}
.field{position:absolute;left:114px;width:381px;background:#fff;border-radius:22px;font-family:'Montserrat',sans-serif;font-size:12px;font-weight:600;color:var(--ink);padding:14px 0 0 26px}
.submit{left:119px;top:3907px;width:154px;height:41px;background:var(--teal-dark);color:#fff;font-size:12px}

/* footer */
.foot-brand{left:136px;top:4060px;width:200px;display:flex;flex-direction:column;align-items:center}
.foot-brand .brand-dot{width:70px;height:70px;margin-bottom:14px}
.foot-brand .brand-name{font-size:46px}
.foot-head{position:absolute;top:4062px;font-family:'Montserrat',sans-serif;font-weight:700;font-size:14px;color:var(--teal);letter-spacing:.5px}
.foot-list{position:absolute;top:4096px;list-style:none;font-size:12.5px;color:var(--ink);line-height:27.8px}
.contact-line{position:absolute;left:864px;font-size:12.5px;color:var(--ink)}
.contact-ico{position:absolute;left:840px}
.social{position:absolute;top:4218px;width:30px;height:30px;border-radius:50%;background:var(--green)}
.foot-bar{position:absolute;left:0;top:4312px;width:1200px;height:55px;background:var(--foot-bar);text-align:center;font-size:11px;line-height:55px;color:#6b7078}
</style>
</head>
<body>

<!-- Header -->
<header class="site-header">
  <a class="nav active" style="left:151px">HOME</a>
  <a class="nav" style="left:241px">ABOUT US</a>
  <a class="nav" style="left:352px">OUR SERVICES</a>
  <a class="nav" style="left:693px">WHY CHOOSE US</a>
  <a class="nav" style="left:849px">TESTIMONIALS</a>
  <a class="nav" style="left:988px">CONTACT US</a>
  <div class="call-btn">
    <svg width="15" height="15" viewBox="0 0 24 24"><path fill="#fff" d="M6.6 10.8a15.1 15.1 0 0 0 6.6 6.6l2.2-2.2c.3-.3.7-.4 1-.2 1.1.4 2.3.6 3.6.6.6 0 1 .4 1 1V20c0 .6-.4 1-1 1A17 17 0 0 1 3 4c0-.6.4-1 1-1h3.5c.6 0 1 .4 1 1 0 1.3.2 2.5.6 3.6.1.3 0 .7-.2 1z"/></svg>
    CALL US NOW +123 555 0142
  </div>
</header>
<div class="brand-badge" aria-label="Quill Physical Therapy">
  <div class="brand-dot"></div>
  <div class="brand-name">QUILL</div>
</div>

<!-- Hero -->
<section class="hero">
  <div class="photo hero-photo" role="img" aria-label="Photo of a therapist massaging a smiling woman's shoulders and neck"></div>
  <div class="abs hero-kicker">WELCOME TO</div>
  <h1 class="abs hero-title">QUILL PHYSICAL</h1>
  <div class="abs hero-sub">THERAPY &amp; WELLNESS</div>
  <a class="btn-pill hero-btn">BOOK APPOINTMENT
    <svg width="22" height="12" viewBox="0 0 22 12"><path d="M0 6h20M15 1l5 5-5 5" stroke="#fff" stroke-width="1.6" fill="none"/></svg>
  </a>
  <svg class="hero-arrow" style="left:26px" width="22" height="38" viewBox="0 0 22 38"><path d="M19 2 3 19l16 17" stroke="#8a9aa3" stroke-width="4" fill="none"/></svg>
  <svg class="hero-arrow" style="left:1160px" width="22" height="38" viewBox="0 0 22 38"><path d="M3 2l16 17L3 36" stroke="#9fcfe0" stroke-width="4" fill="none"/></svg>
</section>

<!-- Feature cards -->
<div class="feature card-green">
  <h3>PHYSICAL<br><b>THERAPY EXPERTS</b></h3>
  <p>Lorem ipsum dolor sit amet, consectetur adipi</p>
  <div class="mini-btn">LEARN MORE</div>
</div>
<div class="feature card-teal">
  <h3>BOOK YOUR<br><b>APPOINTMENT NOW</b></h3>
  <p style="width:240px">Lorem ipsum dolor sit amet, consectetur adipi-scing elit, sed do eiusmod tempor incididunt ut labore et dolore magna aliqua.</p>
  <div class="mini-btn">BOOK NOW</div>
</div>
<div class="feature card-blue">
  <h3>INJURY RELIEF<br><b>&amp; WELLNESS CENTER</b></h3>
  <p>Lorem ipsum dolor sit amet, consectetur adipi</p>
  <div class="mini-btn">LEARN MORE</div>
</div>

<!-- About -->
<div class="abs about-ring"></div>
<div class="abs about-ring2"></div>
<div class="photo about-photo" role="img" aria-label="Photo of a therapist stretching a patient lying on a treatment mat"></div>
<div class="kicker" style="left:595px;top:1020px">WHO WE ARE</div>
<h2 class="section-title" style="left:594px;top:1042px;font-size:38px">ABOUT QUILL</h2>
<p class="abs about-text">Lorem Ipsum is simply dummy text of the printing and type-<br>setting industry. Lorem Ipsum has been the industry's stan-<br>dard dummy text ever since the 1500s, when an unknown<br>printer took a galley of type and scrambled it to make a type<br>specimen book. It has survived not only five centuri</p>
<a class="btn-pill abs outline-btn">LEARN MORE</a>

<!-- Services -->
<section class="services"></section>
<div class="kicker" style="left:110px;top:1649px;font-size:15px">WHAT WE DO</div>
<h2 class="section-title" style="left:109px;top:1678px;font-size:34px">OUR SERVICES</h2>
<div class="bar" style="left:110px;top:1729px;width:114px"></div>
<p class="abs services-text">Lorem Ipsum is simply dummy text of<br>the printing and typesetting industry.<br>Lorem Ipsum has been the industry's<br>standard dummy text ever</p>
<a class="btn-pill abs services-btn">LEARN MORE</a>
<div class="photo services-art" role="img" aria-label="Illustration of a spine silhouette blending into therapy photos"></div>
<div class="photo services-photo" role="img" aria-label="Photo of hands treating a patient's shoulder"></div>
<svg class="abs" style="left:600px;top:1545px" width="300" height="520" viewBox="0 0 300 520">
  <path d="M52 6 A255 255 0 0 1 52 514" stroke="var(--teal)" stroke-width="5" fill="none"/>
</svg>
<div class="svc-icon" style="left:730px;top:1564px"><svg width="32" height="32" viewBox="0 0 32 32" fill="none" stroke="#fff" stroke-width="1.8"><circle cx="16" cy="7" r="4"/><path d="M8 28v-9a8 8 0 0 1 16 0v9M4 28h24"/></svg></div>
<div class="svc-icon" style="left:814px;top:1681px"><svg width="32" height="32" viewBox="0 0 32 32" fill="none" stroke="#fff" stroke-width="1.8"><rect x="4" y="18" width="24" height="6" rx="2"/><circle cx="10" cy="12" r="3"/><path d="M14 14h10M7 24v4M25 24v4"/></svg></div>
<div class="svc-icon" style="left:824px;top:1819px"><svg width="32" height="32" viewBox="0 0 32 32" fill="none" stroke="#fff" stroke-width="1.8"><path d="M16 27S5 20 5 12a5.5 5.5 0 0 1 11-1 5.5 5.5 0 0 1 11 1c0 8-11 15-11 15z"/></svg></div>
<div class="svc-icon" style="left:766px;top:1937px"><svg width="34" height="32" viewBox="0 0 34 32" fill="none" stroke="#fff" stroke-width="1.8"><circle cx="8" cy="22" r="5"/><circle cx="26" cy="22" r="5"/><path d="M12 19l10-10M22 19 12 9"/></svg></div>
<div class="svc-title" style="left:825px;top:1565px">Injury Pain Relief</div>
<div class="svc-text" style="left:826px;top:1592px">Donec convallis pede venenatis<br>nibh Duis quam Nam eget lac</div>
<div class="svc-title" style="left:902px;top:1673px">Physical Theapy</div>
<div class="svc-text" style="left:903px;top:1700px">Donec convallis pede venenatis<br>nibh Duis quam Nam eget lac</div>
<div class="svc-title" style="left:904px;top:1821px">Wellness Service</div>
<div class="svc-text" style="left:905px;top:1848px">Donec convallis pede venenatis<br>nibh Duis quam Nam eget lac</div>
<div class="svc-title" style="left:858px;top:1948px">Join Relief</div>
<div class="svc-text" style="left:856px;top:1975px">Donec convallis pede venenatis<br>nibh Duis quam Nam eget lac</div>

<!-- Success stories band -->
<svg class="abs stories-band" width="1200" height="790" viewBox="0 0 1200 790">
  <defs>
    <linearGradient id="bandGrad" x1="0" y1="0" x2="1" y2="1">
      <stop offset="0" stop-color="#1f9c97"/><stop offset="1" stop-color="#0b625f"/>
    </linearGradient>
  </defs>
  <path d="M0 90 C300 10 700 130 1200 12 V720 H0Z" fill="var(--green)"/>
  <path d="M0 80 C320 20 700 150 1200 40 V700 H0Z" fill="url(#bandGrad)"/>
  <path d="M0 790 V690 C200 600 420 640 700 690 C900 725 1080 690 1200 660 V790Z" fill="var(--green)"/>
  <path d="M0 790 V720 C200 640 420 650 700 700 C900 735 1080 700 1200 680 V790Z" fill="#fff"/>
</svg>
<div class="abs band-kicker">TESTIMONIALS</div>
<h2 class="abs band-title">SUCCESS STORIES</h2>
<div class="bar" style="left:546px;top:2286px;width:108px"></div>

<div class="story" style="left:117px;top:2326px;width:486px;height:383px">
  <div class="photo story-photo" style="width:486px;height:268px;background:linear-gradient(120deg,#dfe8ec,#c9b4a6 45%,#6aa7c6 60%,#e3e9eb)" role="img" aria-label="Photo of a therapist assisting a woman with a shoulder stretch"></div>
  <h4 style="left:30px;top:290px;font-size:13px;line-height:17px;width:430px">Lorem ipsum dolor sit amet, consectetur adipiscing elit, sed do eiusmod tempor incididunt</h4>
  <p style="left:30px;top:330px;font-size:10.5px;line-height:15px;width:420px">enim ad minim veniam, quis nostrud exercitation ullamco laboris nisi ut aliquip ex ea commodo consequat. Duis aute irure dolor in</p>
</div>
<div class="story" style="left:612px;top:2327px;width:446px;height:182px">
  <div class="photo story-photo" style="width:215px;height:182px;background:linear-gradient(120deg,#e8dcd4,#c9a896 50%,#5c6a78)" role="img" aria-label="Photo of a facial wellness treatment"></div>
  <h4 style="left:240px;top:40px;font-size:11.5px;line-height:16px;width:190px">Lorem ipsum dolor sit ame consectetur adipiscing</h4>
  <p style="left:243px;top:86px;font-size:10px;line-height:16px;width:180px">Anim ad minim veniam, quis nostrud exercitation ullamco laboris nisi ut aliquip ex ea com-modo consequat</p>
</div>
<div class="story" style="left:612px;top:2526px;width:446px;height:180px">
  <div class="photo story-photo" style="width:215px;height:180px;background:linear-gradient(120deg,#eef0ef,#e5d14a 45%,#2c3036 75%)" role="img" aria-label="Photo of a leg exercise with a resistance band"></div>
  <h4 style="left:242px;top:40px;font-size:11.5px;line-height:16px;width:190px">Lorem ipsum dolor sit ame consectetur adipiscing</h4>
  <p style="left:243px;top:84px;font-size:10px;line-height:16px;width:180px">Anim ad minim veniam, quis nostrud exercitation ullamco laboris nisi ut aliquip ex ea com-modo consequat</p>
</div>

<!-- What people say -->
<h2 class="section-title" style="left:0;width:1200px;text-align:center;top:2905px;font-size:29px">WHAT PEOPLE SAYS</h2>
<div class="bar" style="left:564px;top:2949px;width:93px"></div>

<div class="review" style="left:134px">
  <div class="review-photo" style="background:linear-gradient(120deg,#eef2f4,#7bb0d8 55%,#d8dde0)" role="img" aria-label="Photo of a senior patient exercising with a therapist"></div>
  <div class="avatar" role="img" aria-label="Reviewer portrait"></div>
  <p>Lorem ipsum dolor sit amet, consectetur adipiscing elit, sed do eiusmod tempor incididunt ut labore et dolore magna ali-quaUt enim ad minim veniam</p>
  <div class="who">Dana Merrit</div>
  <div class="stars">★★★★★</div>
</div>
<div class="review" style="left:458px">
  <div class="review-photo" style="background:linear-gradient(120deg,#e9eef0,#6e9ec4 40%,#a8a9aa 70%,#e2e6e8)" role="img" aria-label="Photo of a man doing an arm stretch with a therapist"></div>
  <div class="avatar" role="img" aria-label="Reviewer portrait"></div>
  <p>Lorem ipsum dolor sit amet, consectetur adipiscing elit, sed do eiusmod tempor incididunt ut labore et dolore magna ali-quaUt enim ad minim veniam</p>
  <div class="who">Dana Merrit</div>
  <div class="stars">★★★★★</div>
</div>
<div class="review" style="left:780px">
  <div class="review-photo" style="background:linear-gradient(120deg,#e8dcd4,#c9a896 50%,#4f5a66)" role="img" aria-label="Photo of a facial wellness treatment"></div>
  <div class="avatar" role="img" aria-label="Reviewer portrait"></div>
  <p>Lorem ipsum dolor sit amet, consectetur adipiscing elit, sed do eiusmod tempor incididunt ut labore et dolore magna ali-quaUt enim ad minim veniam</p>
  <div class="who">Dana Merrit</div>
  <div class="stars">★★★★★</div>
</div>
<div class="dot" style="left:548px"></div>
<div class="dot" style="left:595px"></div>
<div class="dot" style="left:641px;background:var(--green)"></div>

<!-- Appointment -->
<section class="appt"></section>
<div class="photo appt-photo" role="img" aria-label="Photo of a therapist guiding a woman through a shoulder stretch"></div>
<div class="abs head-font" style="left:119px;top:3550px;color:#fff;font-size:15px;font-weight:600;letter-spacing:3px">GET IN TOUCH</div>
<h2 class="abs head-font" style="left:118px;top:3567px;color:#fff;font-size:30px;font-weight:700;letter-spacing:1px">BOOK APPOINTMENT</h2>
<div class="field" style="top:3632px;height:45px">Name*</div>
<div class="field" style="top:3683px;height:44px">Email address*</div>
<div class="field" style="top:3734px;height:44px">Phone*</div>
<div class="field" style="top:3792px;height:93px;border-radius:14px;padding-top:12px">Message</div>
<a class="btn-pill abs submit">SUBMIT NOW</a>

<!-- Footer -->
<div class="abs foot-brand" aria-label="Quill Physical Therapy">
  <div class="brand-dot"></div>
  <div class="brand-name">QUILL</div>
</div>
<div class="foot-head" style="left:422px">QUICK LINKS</div>
<ul class="foot-list" style="left:426px"><li>Home</li><li>About Us</li><li>Our Services</li><li>New Products</li><li>Contact Us</li></ul>
<div class="foot-head" style="left:619px">RESOURCES</div>
<ul class="foot-list" style="left:623px"><li>News</li><li>Testimonials</li><li>Privacy Policy</li><li>Terms &amp; Condition</li></ul>
<div class="foot-head" style="left:836px">CONTACT US</div>
<svg class="contact-ico" style="top:4104px" width="14" height="18" viewBox="0 0 14 18"><path d="M7 0a7 7 0 0 0-7 7c0 5 7 11 7 11s7-6 7-11a7 7 0 0 0-7-7zm0 10a3 3 0 1 1 0-6 3 3 0 0 1 0 6z" fill="var(--teal)"/></svg>
<div class="contact-line" style="top:4105px">Office Lindenau | Birkenweg 14</div>
<div class="contact-line" style="top:4129px">Office Rheinfeld | Muehlegasse 9</div>
<svg class="contact-ico" style="top:4152px" width="14" height="14" viewBox="0 0 24 24"><path fill="var(--teal)" d="M6.6 10.8a15.1 15.1 0 0 0 6.6 6.6l2.2-2.2c.3-.3.7-.4 1-.2 1.1.4 2.3.6 3.6.6.6 0 1 .4 1 1V20c0 .6-.4 1-1 1A17 17 0 0 1 3 4c0-.6.4-1 1-1h3.5c.6 0 1 .4 1 1 0 1.3.2 2.5.6 3.6.1.3 0 .7-.2 1z"/></svg>
<div class="contact-line" style="top:4153px">Tel: (1300) 555 0187</div>
<svg class="contact-ico" style="top:4178px" width="15" height="11" viewBox="0 0 15 11"><rect width="15" height="11" rx="1" fill="var(--teal)"/><path d="M1 1l6.5 5L14 1" stroke="#fff" stroke-width="1.2" fill="none"/></svg>
<div class="contact-line" style="top:4175px">Email: hello@quillpt.com</div>
<div class="social" style="left:848px"></div>
<div class="social" style="left:884px"></div>
<div class="social" style="left:920px"></div>
<div class="social" style="left:957px"></div>

<div class="foot-bar">© 2021 Quill | All Rights Reserved &nbsp;|&nbsp; Terms &amp; Condition</div>

</body>
</html>
```